CrestwayGuide,Christian faith-based firm providing personal,professional & organizational consulting

2 designs needed for retractable signs (size 33.5" x 79"):
1. For Firm (CrestwayGuide)
We believe:
*That not-for-profit organizations make the most important investments in changing lives and transforming communities
*That vision must be at the core of every organization;
*That organizational outcomes should be transformative;
*That impactful leadership is driven and directed by vision clarity, vision strategy, and vision execution; and
*That organizational insight and collaborative strategy results in sound solutions.

Services Provided:
As a full service and comprehensive firm, our capabilities include:
*Vision Discovery, Clarity and Execution
*Organizational Strategy Formation, Action Planning and Execution
*Leadership Excellence and Team Development
*Retreats, Conferences and Workshops for capacity building
*Executive and Administrative Services
*Project Planning, Management and Synergy

2. For the Women's Retreat the Firm hosts annually (Gentle and Gathered In Women's Retreat)
This ministry is established to facilitate and be a conduit by which women are empowered in their Personal, Professional, and Spiritual lives to fulfill the best that God has designed for them".

Target Market(s)

Professionals, Non-Profit, Faith Based Organizations - CrestwayGuide sign
Faith Based women, diverse, multi-cultural - Gentle and Gathered In sign

Font styles to use
Serif

Colors
fbed22
ffffff
1b1b1b

Requirements
Must have
• Use of logos, colors to include firm colors of black, gold and white (all or in part).
• 1. CrestwayGuide design - the words and images for
• i. VISION
• ii. ORGANIZATIONAL STRATEGY
• iii. LEADERSHIP DEVELOPMENT
• iv. PROJECT PLANNING & MANAGEMENT
• (www.crestwayguide.example)
• 2. Gentle and Gathered In design - incorporate images and words to reflect-"Gentle and Gathered In. Is a part of the Women's Ministry arm of CrestwayGuide, Inc. This ministry is established to facilitate and be a conduit by which women are EMPOWERED in their Personal, Professional, and Spiritual lives to fulfill the best that God has designed for them".

```html
<!DOCTYPE html>
<html lang="en">
<head>
<meta charset="utf-8">
<title>CrestwayGuide Retractable Signs</title>
<link rel="stylesheet" href="https://fonts.googleapis.com/css2?family=Cormorant+Garamond:wght@600&family=Open+Sans:wght@300;400;600;700&family=Montserrat:wght@800&display=swap">
<style>
  :root {
    --gold: #d9bd7a;
    --gold-bright: #fbed22;
    --gold-deep: #b8975a;
    --ink: #1b1b1b;
    --black: #0c0c0c;
    --white: #ffffff;
    --page: #f2f2f2;
  }
  * { box-sizing: border-box; margin: 0; padding: 0; }
  html, body { width: 1200px; height: 2317px; overflow: hidden; }
  body {
    background: var(--page);
    font-family: "Open Sans", Arial, sans-serif;
    color: var(--white);
    position: relative;
  }
  .sign {
    position: absolute;
    top: 522px;
    width: 540px;
    height: 1273px;
    background: radial-gradient(ellipse at 50% 30%, #262626 0%, var(--ink) 45%, var(--black) 100%);
    box-shadow: 0 18px 40px rgba(0,0,0,0.35);
    overflow: hidden;
  }
  .sign--firm { left: 40px; }
  .sign--retreat { left: 620px; }

  .brand { position: absolute; top: 62px; left: 0; right: 0; text-align: center; }
  .brand__dot {
    display: block; width: 44px; height: 44px; margin: 0 auto 14px;
    border-radius: 50%; background: var(--gold);
  }
  .brand__name {
    font-family: "Cormorant Garamond", Georgia, serif;
    font-weight: 600; font-size: 52px; line-height: 1; color: var(--white);
  }
  .brand__tagline {
    margin-top: 8px; font-size: 13px; font-weight: 600; letter-spacing: 0.5px;
    color: var(--gold);
  }

  /* Firm sign */
  .firm-body { position: absolute; top: 232px; left: 26px; right: 26px; }
  .section-title { font-size: 30px; font-weight: 300; letter-spacing: 0.5px; line-height: 1.1; }
  .section-title strong { color: var(--gold); font-weight: 700; }
  .section-title .upper { text-transform: uppercase; }
  .section-sub {
    margin-top: 6px; font-size: 19px; font-weight: 700; color: var(--gold);
    text-transform: uppercase; line-height: 1.25;
  }
  .point-list { list-style: none; margin-top: 18px; }
  .point-list li {
    position: relative; padding-left: 22px; font-size: 15.5px; line-height: 1.45;
    margin-bottom: 18px;
  }
  .point-list li::before {
    content: ""; position: absolute; left: 2px; top: 8px; width: 8px; height: 8px;
    border-radius: 50%; background: var(--gold);
  }
  .point-list--services li { margin-bottom: 15px; }
  .services { margin-top: 24px; }

  .photo-bridge {
    position: absolute; left: 0; right: 0; bottom: 0; height: 420px;
    background: linear-gradient(180deg, rgba(27,27,27,0) 0%, #8d8d8d 28%, #cfcfcf 50%, #7a7a7a 72%, #262626 100%);
  }

  .site-url {
    position: absolute; left: 0; right: 0; bottom: 42px; text-align: center;
    font-size: 27px; font-weight: 600; color: var(--white);
  }

  /* Retreat sign */
  .host { position: absolute; top: 212px; left: 0; right: 0; text-align: center; }
  .host__title {
    font-family: "Montserrat", Arial, sans-serif; font-weight: 800;
    font-size: 40px; letter-spacing: 1px; color: var(--gold);
  }
  .host__event { font-size: 21px; font-weight: 400; margin-top: 2px; }

  .retreat-mark { position: absolute; top: 318px; left: 0; right: 0; text-align: center; }
  .retreat-mark__name {
    font-family: "Cormorant Garamond", Georgia, serif; font-weight: 600;
    font-size: 38px; color: var(--gold); line-height: 1.1;
  }
  .retreat-mark__rule { width: 110px; height: 2px; margin: 26px auto 0; background: var(--gold-deep); }

  .mission { position: absolute; top: 458px; left: 30px; right: 30px; text-align: center; }
  .quote-mark {
    font-family: "Montserrat", Arial, sans-serif; font-weight: 800;
    font-size: 78px; line-height: 0.6; color: var(--gold); height: 44px;
  }
  .mission__text { font-size: 20px; font-weight: 700; line-height: 1.45; margin: 16px 0 26px; }
  .mission__text strong { color: var(--gold); font-weight: 800; }

  .photo-hands {
    position: absolute; left: 0; right: 0; top: 800px; height: 400px;
    background: radial-gradient(ellipse at 50% 45%, #9a9a9a 0%, #4a4a4a 40%, var(--ink) 75%);
  }
</style>
</head>
<body>

  <section class="sign sign--firm">
    <header class="brand">
      <span class="brand__dot"></span>
      <div class="brand__name">CrestwayGuide</div>
      <div class="brand__tagline">CHANGING LIVES, TRANSFORMING COMMUNITIES</div>
    </header>

    <div class="firm-body">
      <h2 class="section-title">we <strong>BELIEVE</strong></h2>
      <ul class="point-list">
        <li>That not-for-profit organizations make the most important investments in changing lives and transforming communities</li>
        <li>That vision must be at the core of every organization;</li>
        <li>That organizational outcomes should be transformative;</li>
        <li>That impactful leadership is driven and directed by vision clarity, vision strategy, and vision execution; and</li>
        <li>That organizational insight and collaborative strategy results in sound solutions.</li>
      </ul>

      <div class="services">
        <h2 class="section-title"><strong>SERVICES</strong> <span class="upper">Provided</span></h2>
        <p class="section-sub">As a full service and comprehensive firm, our capabilities include:</p>
        <ul class="point-list point-list--services">
          <li>Vision Discovery, Clarity and Execution Organizational Strategy Formation, Action Planning and Execution</li>
          <li>Leadership Excellence and Team Development</li>
          <li>Retreats, Conferences and Workshops for capacity building</li>
          <li>Executive and Administrative Services</li>
          <li>Project Planning, Management and Synergy</li>
        </ul>
      </div>
    </div>

    <div class="photo-bridge" role="img" aria-label="Black and white photo of a suspension bridge tower rising out of fog over the water"></div>
    <p class="site-url">www.crestwayguide.example</p>
  </section>

  <section class="sign sign--retreat">
    <header class="brand">
      <span class="brand__dot"></span>
      <div class="brand__name">CrestwayGuide</div>
      <div class="brand__tagline">CHANGING LIVES, TRANSFORMING COMMUNITIES</div>
    </header>

    <div class="host">
      <h2 class="host__title">WE HOST ANNUALLY</h2>
      <p class="host__event">(Gentle and Gathered In Women's Retreat)</p>
    </div>

    <div class="retreat-mark">
      <div class="retreat-mark__name">Gentle and<br>Gathered In</div>
      <div class="retreat-mark__rule"></div>
    </div>

    <div class="mission">
      <div class="quote-mark">&ldquo;</div>
      <p class="mission__text">Gentle and Gathered In. Is a part of the Women's Ministry arm of CrestwayGuide, Inc. This ministry is established to facilitate and be a conduit by which women are <strong>EMPOWERED</strong> in their Personal, Professional, and Spiritual lives to fulfill the best that God has designed for them.</p>
      <div class="quote-mark">&rdquo;</div>
    </div>

    <div class="photo-hands" role="img" aria-label="Black and white photo of folded hands in prayer holding a rosary with a cross"></div>
    <p class="site-url">www.crestwayguide.example</p>
  </section>

</body>
</html>
```